BOLD & MINIMALIST DESIGN NEEDED

We want a very bold but minimalistic business card design that is impactful and utilizes both sides of the business card. Our current logo is included for your use.

We want bold fonts and good use of negative space. We don't want the logo to overpower the design.

Target Market(s)

Professionals who are building new commercial buildings.

Industry/Entity Type

Construction

Contact Information for Business Card

Name, Title, email, office phone, cell phone, website

Font styles to use
Serif
Sans Serif

Requirements
Must have
• Bold design!

```html
<!DOCTYPE html>
<html lang="en">
<head>
<meta charset="utf-8">
<title>Ridgeline Design + Build — Business Card</title>
<link rel="stylesheet" href="https://fonts.googleapis.com/css2?family=Fira+Sans:wght@400;500;800&display=swap">
<style>
  :root {
    --backdrop: #1d1d1f;
    --brand-green: #86c229;
    --ink: #0b0b0d;
    --paper: #ffffff;
    --card-w: 880px;
    --card-h: 503px;
    --radius: 30px;
  }
  * { box-sizing: border-box; margin: 0; padding: 0; }
  html, body {
    width: 1200px; height: 1122px; overflow: hidden;
    background: var(--backdrop);
    font-family: "Fira Sans", Arial, sans-serif;
  }
  .canvas {
    width: 1200px; height: 1122px;
    display: flex; flex-direction: column; align-items: center; justify-content: center;
    gap: 40px;
  }
  .card {
    position: relative;
    width: var(--card-w); height: var(--card-h);
    border-radius: var(--radius);
    overflow: hidden;
    box-shadow: 0 14px 30px rgba(0,0,0,.5);
  }
  .card-swoosh { position: absolute; inset: 0; width: 100%; height: 100%; }

  /* Contact side */
  .card--contact { background: var(--brand-green); }
  .contact-block { position: absolute; left: 70px; top: 80px; }
  .contact-name {
    font-weight: 800; font-size: 46px; letter-spacing: 1px;
    color: var(--ink); line-height: 1;
  }
  .contact-title {
    font-weight: 400; font-size: 27px; letter-spacing: 1px;
    color: var(--paper); margin-top: 4px;
  }
  .contact-list { list-style: none; margin-top: 18px; }
  .contact-item {
    display: flex; align-items: center; gap: 14px;
    font-size: 25px; font-weight: 400; letter-spacing: 1px;
    color: var(--paper); line-height: 1.28;
  }
  .contact-icon { width: 20px; height: 20px; flex: none; fill: var(--ink); }

  /* Brand side */
  .card--brand { background: var(--paper); }
  .brand-lockup {
    position: absolute; left: 440px; top: 195px;
    display: flex; align-items: center; gap: 16px;
  }
  .brand-mark { width: 34px; height: 34px; background: var(--brand-green); flex: none; }
  .brand-name {
    font-weight: 800; font-size: 46px; line-height: 1.05;
    color: var(--ink); letter-spacing: 1px;
  }
</style>
</head>
<body>
<main class="canvas">

  <section class="card card--contact" aria-label="Contact side">
    <svg class="card-swoosh" viewBox="0 0 880 503" preserveAspectRatio="none" aria-hidden="true">
      <path d="M300 425 Q600 375 880 470 L880 540 Q640 420 300 425 Z" fill="var(--ink)"/>
    </svg>
    <div class="contact-block">
      <h1 class="contact-name">MARCUS HALE</h1>
      <p class="contact-title">Founder &amp; CEO</p>
      <ul class="contact-list">
        <li class="contact-item">
          <svg class="contact-icon" viewBox="0 0 24 24"><path d="M6.6 10.8a15 15 0 0 0 6.6 6.6l2.2-2.2c.3-.3.7-.4 1-.2 1.1.4 2.3.6 3.6.6.6 0 1 .4 1 1V20c0 .6-.4 1-1 1A17 17 0 0 1 3 4c0-.6.4-1 1-1h3.5c.6 0 1 .4 1 1 0 1.3.2 2.5.6 3.6.1.3 0 .7-.2 1z"/></svg>
          (123) 456-7890
        </li>
        <li class="contact-item">
          <svg class="contact-icon" viewBox="0 0 24 24"><path d="M7 2h10a2 2 0 0 1 2 2v16a2 2 0 0 1-2 2H7a2 2 0 0 1-2-2V4a2 2 0 0 1 2-2zm0 3v13h10V5zm5 14.2a1 1 0 1 0 0 1.6 1 1 0 0 0 0-1.6z"/></svg>
          (123) 456-7890
        </li>
        <li class="contact-item">
          <svg class="contact-icon" viewBox="0 0 24 24"><path d="M2 5h20v14H2zm2 2v.5l8 5 8-5V7zm0 2.8V17h16V9.8l-8 5z"/></svg>
          info@ridgelinebuild.com
        </li>
        <li class="contact-item">
          <svg class="contact-icon" viewBox="0 0 24 24"><path d="M12 2a10 10 0 1 0 0 20 10 10 0 0 0 0-20zm6.9 6h-3a15 15 0 0 0-1.3-3.9A8 8 0 0 1 18.9 8zM12 4c.8 1.2 1.5 2.5 1.9 4h-3.8c.4-1.5 1.1-2.8 1.9-4zM4.3 14a8 8 0 0 1 0-4h3.4a16 16 0 0 0 0 4zm.8 2h3a15 15 0 0 0 1.3 3.9A8 8 0 0 1 5.1 16zm3-8h-3a8 8 0 0 1 4.3-3.9A15 15 0 0 0 8.1 8zM12 20c-.8-1.2-1.5-2.5-1.9-4h3.8c-.4 1.5-1.1 2.8-1.9 4zm2.3-6H9.7a14 14 0 0 1 0-4h4.6a14 14 0 0 1 0 4zm.3 5.9a15 15 0 0 0 1.3-3.9h3a8 8 0 0 1-4.3 3.9zm1.7-5.9a16 16 0 0 0 0-4h3.4a8 8 0 0 1 0 4z"/></svg>
          ridgelinebuild.com
        </li>
      </ul>
    </div>
  </section>

  <section class="card card--brand" aria-label="Brand side">
    <svg class="card-swoosh" viewBox="0 0 880 503" preserveAspectRatio="none" aria-hidden="true">
      <path d="M0 245 Q270 270 430 503 L395 503 Q240 330 0 300 Z" fill="var(--ink)"/>
    </svg>
    <div class="brand-lockup">
      <span class="brand-mark" aria-hidden="true"></span>
      <p class="brand-name">RIDGELINE<br>DESIGN + BUILD</p>
    </div>
  </section>

</main>
</body>
</html>
```